Corvane Freight Company Business Card Design

We are a company that delivers natural saltwater (from the ocean) to aquarium companies, restaurants and home marine tanks. I would like a new business card to suit.

Must include Name, company name, abn, contact number and website as well as logo (see attached).

Looking for a design that stands out, has a clean but unique appearance.

Double and single sided entries welcome

Business

• Logo

```html
<!DOCTYPE html>
<html lang="en">
<head>
<meta charset="utf-8">
<title>Corvane Freight Company – Business Card</title>
<link rel="stylesheet" href="https://fonts.googleapis.com/css2?family=Source+Sans+3:wght@400;600;700&display=swap">
<style>
  :root {
    --backdrop: #1f1f20;
    --front-blue: #1f5ef0;
    --strip-light: #9fe9fb;
    --strip-pale: #d8f7ff;
    --back-center: #e4fbff;
    --back-edge: #6fe7fb;
    --white: #ffffff;
    --text-soft: #e6eeff;
  }
  * { margin: 0; padding: 0; box-sizing: border-box; }
  html, body {
    width: 1200px; height: 1123px; overflow: hidden;
    background: var(--backdrop);
    font-family: "Source Sans 3", "Myriad Pro", Arial, sans-serif;
  }
  .canvas { position: relative; width: 1200px; height: 1123px; }

  .card { position: absolute; width: 809px; height: 463px; overflow: hidden; }

  /* Front */
  .card-front { left: 77px; top: 72px; background: var(--front-blue); }
  .side-strip {
    position: absolute; left: 0; top: 0; width: 97px; height: 100%;
    background: linear-gradient(180deg, var(--strip-light) 0%, var(--strip-pale) 55%, var(--strip-light) 100%);
  }
  .strip-rule {
    position: absolute; left: 102px; top: 0; width: 4px; height: 100%;
    background: var(--strip-pale);
  }
  .brand-front {
    position: absolute; left: 60px; top: 60px;
    display: flex; align-items: center; gap: 16px;
  }
  .brand-dot { width: 34px; height: 34px; border-radius: 50%; background: var(--white); flex: none; }
  .brand-name {
    color: var(--white); font-weight: 700; font-size: 50px; line-height: 1.05;
    letter-spacing: -0.5px;
  }
  .contact-list {
    position: absolute; left: 128px; top: 272px;
    list-style: none; color: var(--text-soft); font-size: 20px; line-height: 31px;
  }
  .contact-list li { display: flex; align-items: center; gap: 8px; }
  .contact-list svg { width: 16px; height: 16px; flex: none; }
  .holder {
    position: absolute; right: 28px; top: 302px; text-align: right; color: var(--white);
  }
  .holder-name { font-weight: 700; font-size: 25px; line-height: 30px; }
  .holder-title { font-size: 19px; line-height: 24px; color: var(--text-soft); }
  .company-block {
    position: absolute; left: 128px; top: 384px; color: var(--text-soft);
    font-size: 20px; line-height: 28px;
  }
  .company-name { font-weight: 700; color: var(--white); }

  /* Back */
  .card-back {
    left: 300px; top: 582px;
    background: radial-gradient(ellipse 60% 70% at 52% 45%, var(--back-center) 0%, #b4f3fd 45%, var(--back-edge) 100%);
  }
  .brand-back {
    position: absolute; left: 0; right: 0; top: 175px; text-align: center;
    color: var(--front-blue); font-weight: 700; font-size: 56px; line-height: 1.05;
  }
  .back-site {
    position: absolute; left: 0; right: 0; top: 370px; text-align: center;
    color: var(--white); font-size: 24px; letter-spacing: 5px;
  }
</style>
</head>
<body>
<main class="canvas">
  <section class="card card-front" aria-label="Business card front">
    <div class="side-strip"></div>
    <div class="strip-rule"></div>

    <div class="brand-front">
      <span class="brand-dot"></span>
      <span class="brand-name">Corvane Freight<br>Company</span>
    </div>

    <ul class="contact-list">
      <li>
        <svg viewBox="0 0 16 16" aria-hidden="true"><circle cx="8" cy="8" r="7" fill="none" stroke="#fff" stroke-width="1.4"/><path d="M5.5 4.5c.6-.4 1.2 0 1.4.6l.3 1c.1.4-.1.7-.4.9l-.4.3c.4 1 1.1 1.8 2.1 2.2l.3-.4c.2-.3.6-.5 1-.4l1 .3c.6.2.9.8.5 1.4-.6.8-1.5 1-2.4.6-2-.9-3.4-2.4-4.1-4.4-.3-.8 0-1.6.7-2.1z" fill="#fff"/></svg>
        123-456-7890
      </li>
      <li>
        <svg viewBox="0 0 16 16" aria-hidden="true"><circle cx="8" cy="8" r="7" fill="#fff"/><path d="M1 8h14M8 1c-2.5 2-2.5 12 0 14M8 1c2.5 2 2.5 12 0 14" fill="none" stroke="#1f5ef0" stroke-width="1"/></svg>
        www.website.com
      </li>
      <li>ABN : 0123456789</li>
    </ul>

    <div class="holder">
      <p class="holder-name">Your name</p>
      <p class="holder-title">Title</p>
    </div>

    <div class="company-block">
      <p class="company-name">Corvane Freight Co.</p>
      <p>Street Name, City Name, State, City Zip Code</p>
    </div>
  </section>

  <section class="card card-back" aria-label="Business card back">
    <p class="brand-back">Corvane Freight<br>Company</p>
    <p class="back-site">www.website.com</p>
  </section>
</main>
</body>
</html>
```